Customer Value Leaflet

We need a bi-fold brochure designing, based on the attached PDF wireframes. Our company name is brambleharvik.com (of which the logo is currently being designed). The corporate colour is orange (the exact shade of which we are happy to leave to the designers discretion).

The leaflet will distributed to customer experience experts and marketers so the design needs to be bright, engaging, clean and simple. Design is critical.

It Company

```html
<!DOCTYPE html>
<html lang="en">
<head>
<meta charset="utf-8">
<title>Customer Value Leaflet</title>
<link rel="stylesheet" href="https://fonts.googleapis.com/css2?family=Raleway:wght@300;400;600;700&display=swap">
<style>
  :root {
    --orange: #f0772f;
    --orange-soft: #f58d4a;
    --blue: #3ea4d2;
    --ink: #2b2b2b;
    --paper: #ffffff;
    --backdrop: #e9e9e9;
    --fold: #dcdcdc;
  }
  * { box-sizing: border-box; margin: 0; padding: 0; }
  html, body { width: 1200px; height: 799px; overflow: hidden; }
  body {
    background: var(--backdrop);
    font-family: "Raleway", Arial, sans-serif;
    color: var(--ink);
    position: relative;
  }
  .brochure {
    position: absolute;
    left: 60px; top: 140px;
    width: 1080px; height: 520px;
    display: flex;
    background: var(--paper);
  }
  .panel {
    position: relative;
    width: 360px; height: 520px;
    border-right: 1px solid var(--fold);
    overflow: hidden;
  }
  .panel:last-child { border-right: none; }

  /* Left panel */
  .clv-header {
    position: absolute; left: 0; top: 24px;
    width: 336px; height: 42px;
    background: var(--orange);
    border-radius: 0 14px 0 0;
    color: #fff; font-size: 18px; font-weight: 400;
    display: flex; align-items: center; justify-content: center;
    letter-spacing: .3px;
  }
  .persona-art {
    position: absolute; width: 62px; height: 62px;
    border-radius: 50%;
    border: 2px solid var(--ink);
  }
  .persona-art--kim { left: 26px; top: 98px; background: radial-gradient(circle, #e9c6a8 0%, #d98a52 70%); }
  .persona-art--kevin { left: 276px; top: 80px; background: radial-gradient(circle, #c9d7a8 0%, #8ea86a 70%); }
  .persona-name {
    position: absolute; font-size: 16px; font-weight: 400; letter-spacing: 3px;
  }
  .persona-name--kim { left: 94px; top: 108px; }
  .persona-name--kevin { left: 206px; top: 88px; }
  .optimise-arrow { position: absolute; left: 148px; top: 76px; }
  .clv-figure {
    position: absolute; font-size: 21px; font-weight: 400; color: var(--orange);
    white-space: nowrap;
  }
  .clv-figure--kim { left: 14px; top: 178px; }
  .clv-figure--kevin { left: 208px; top: 170px; }
  .clv-note {
    position: absolute; font-size: 12.5px; line-height: 1.25; font-weight: 400;
    color: var(--orange-soft); text-align: center;
  }
  .clv-note--kim { left: 10px; top: 210px; width: 134px; }
  .clv-note--kevin { left: 204px; top: 202px; width: 142px; }
  .clv-summary {
    position: absolute; left: 18px; top: 318px; width: 324px;
    font-size: 14px; line-height: 1.3; color: var(--blue); text-align: center;
  }
  .web-pill {
    position: absolute; left: 0; top: 404px;
    width: 330px; height: 50px;
    background: var(--blue);
    border-radius: 0 25px 25px 0;
    color: #fff; font-size: 22px; font-weight: 400;
    display: flex; align-items: center; justify-content: center;
  }

  /* Middle panel */
  .bubble {
    position: absolute; color: #fff; font-weight: 300;
  }
  .bubble strong { font-weight: 700; }
  .bubble--platform {
    left: 34px; top: 30px; width: 220px; height: 96px;
    background: var(--orange-soft);
    border-radius: 34px 40px 46px 30px;
    padding: 14px 18px; font-size: 14px; line-height: 1.2;
  }
  .pie-row {
    position: absolute; left: 18px; top: 150px;
    display: flex; gap: 22px;
  }
  .bubble--team {
    left: 26px; top: 286px; width: 316px; height: 140px;
    background: var(--blue);
    border-radius: 56px 48px 60px 50px;
    padding: 22px 26px; font-size: 15px; line-height: 1.3;
  }

  /* Right panel */
  .brand-tile {
    position: absolute; left: 118px; top: 22px;
    width: 130px; height: 88px;
    background: var(--orange);
    color: #fff; font-size: 17px; font-weight: 700;
    display: flex; align-items: center; justify-content: center;
  }
  .tagline {
    position: absolute; left: 0; width: 360px; text-align: center;
    font-weight: 400; font-size: 30px;
  }
  .tagline--lead { top: 122px; }
  .tagline--tail { top: 290px; }
  .value-mark { position: absolute; left: 28px; top: 160px; }
  .value-words {
    position: absolute; left: 0; width: 360px; top: 180px;
    text-align: center; color: var(--blue);
    font-size: 42px; font-weight: 600; line-height: 1.1; letter-spacing: 1px;
  }
  .foot-tab {
    position: absolute; left: 126px; top: 364px;
  }
</style>
</head>
<body>
  <main class="brochure">
    <section class="panel panel--clv">
      <div class="clv-header">Once you can calculate CLV</div>

      <div class="persona-art persona-art--kim" role="img" aria-label="Illustration of customer Kim"></div>
      <div class="persona-name persona-name--kim">KIM</div>
      <div class="persona-art persona-art--kevin" role="img" aria-label="Illustration of customer Kevin"></div>
      <div class="persona-name persona-name--kevin">KEVIN</div>

      <svg class="optimise-arrow" width="52" height="232" viewBox="0 0 52 232" aria-label="Optimise your marketing arrow">
        <path d="M14 0 H38 V192 H50 L26 230 L2 192 H14 Z" fill="var(--blue)"/>
        <text x="0" y="0" transform="translate(31 100) rotate(-90)" text-anchor="middle" fill="#fff" font-family="Raleway, Arial, sans-serif" font-size="13">optimise your marketing</text>
      </svg>

      <div class="clv-figure clv-figure--kim">CLV of £149</div>
      <p class="clv-note clv-note--kim">You can personalize Kim's marketing experience to grow her lifetime value to be more like Kevin's</p>
      <div class="clv-figure clv-figure--kevin">CLV of £282</div>
      <p class="clv-note clv-note--kevin">You can understand why Kevin is more valuable and acquire more customers like him</p>

      <p class="clv-summary">We use data and science to predict how your customers will behave in the future. Even if you already use CLV, we can help you do and earn more.</p>
      <div class="web-pill">www.brambleharvik.com</div>
    </section>

    <section class="panel panel--platform">
      <p class="bubble bubble--platform"><strong>VANTORA</strong> is our Cutomer Value Platform, designed for Marketers in the Digital Enterprise.</p>

      <div class="pie-row">
        <svg width="96" height="96" viewBox="0 0 100 100" aria-label="Pie chart">
          <path d="M50 50 L50 5 A45 45 0 0 1 94.3 57.8 Z" fill="#fcd4b8"/>
          <path d="M50 50 L94.3 57.8 A45 45 0 0 1 15.5 78.9 Z" fill="#f7a570"/>
          <path d="M50 50 L15.5 78.9 A45 45 0 0 1 50 5 Z" fill="#f28a45"/>
        </svg>
        <svg width="96" height="96" viewBox="0 0 100 100" aria-label="Pie chart">
          <path d="M50 50 L50 5 A45 45 0 0 1 50 95 Z" fill="#4aa8d8"/>
          <path d="M50 50 L50 95 A45 45 0 0 1 5.7 57.8 Z" fill="#d3e6f4"/>
          <path d="M50 50 L5.7 57.8 A45 45 0 0 1 27.5 11 Z" fill="#a9cfe9"/>
          <path d="M50 50 L27.5 11 A45 45 0 0 1 50 5 Z" fill="#7fb9e0"/>
        </svg>
        <svg width="96" height="96" viewBox="0 0 100 100" aria-label="Pie chart">
          <path d="M50 50 L50 5 A45 45 0 0 1 72.5 89 Z" fill="#333333"/>
          <path d="M50 50 L72.5 89 A45 45 0 0 1 7.7 65.4 Z" fill="#8a8a8a"/>
          <path d="M50 50 L7.7 65.4 A45 45 0 0 1 11 27.5 Z" fill="#cfcfcf"/>
          <path d="M50 50 L11 27.5 A45 45 0 0 1 50 5 Z" fill="#f2f2f2"/>
        </svg>
      </div>

      <p class="bubble bubble--team"><strong>VANTORA</strong> is like having a team of <strong>data scientists</strong> making valuable insights available to your website in real-time so that you can deliver <strong>the ultimate customer experience</strong></p>
    </section>

    <section class="panel panel--cover">
      <div class="brand-tile">Brambleharvik</div>
      <div class="tagline tagline--lead">We're a</div>
      <svg class="value-mark" width="304" height="130" viewBox="0 0 304 130" aria-hidden="true">
        <path d="M150 8 C250 4 300 30 298 66 C296 104 230 124 150 122 C60 120 6 100 6 64 C6 28 70 10 168 10" fill="none" stroke="var(--blue)" stroke-width="3"/>
      </svg>
      <div class="value-words">CUSTOMER<br>VALUE</div>
      <div class="tagline tagline--tail">Company</div>
      <svg class="foot-tab" width="110" height="60" viewBox="0 0 110 60" aria-hidden="true">
        <path d="M12 0 H98 L110 60 H0 Z" fill="var(--orange)"/>
      </svg>
    </section>
  </main>
</body>
</html>
```